Website for Dental Office - The Bright Arch Clinic

The bright arch clinic is a dental office offering cosmetic dentistry, general dentistry, and multi-specialty dental care all under one roof in our state-of-the-art cosmetic dental center. We are particularly striving to provide services that fit the need of the young generation. Thus, we hope to have a modern, professional concise website that represents our spirit.

*Should be able to switch from English to Chinese

6 sections besides homepage:
Home, Meet us, Services,
Patient Info, Cases&Reviews, Blog, Contact

The Services sections should contain multiple subsections such as cleaning and prevention, cosmetic dentistry, implant dentistry, removable dentures, etc...
The Patient Info section is also intended to contain several subsections such as
New Patient offer, accepted Insurance, patient portal, helpful tips, etc...

Target Market(s)

young generation

Coding

Coded - Design and coding required

Number of Pages Required

5+ page

Font styles to use
Sans Serif

Colors
0592cd
33a6d7
85cae6
00a990
33b8a4
86cfc6
cee9f5
cfeae6
3277b5

Requirements
Must have
• *Should be able to switch from English to Chinese
Nice to have
• http://www.thebrightarchclinic.com/
• As a reference, the above link is the current website, but we would like to change the appearance and the content (our new logo's picture is attached)

```html
<!DOCTYPE html>
<html lang="en">
<head>
<meta charset="utf-8">
<title>Reviews – The Bright Arch Clinic</title>
<link href="https://fonts.googleapis.com/css2?family=Montserrat:wght@300;400;500;600;700;800&display=swap" rel="stylesheet">
<style>
:root{
  --blue-deep:#0592cd;
  --blue:#33a6d7;
  --blue-soft:#85cae6;
  --green:#00a990;
  --green-mid:#33b8a4;
  --green-soft:#86cfc6;
  --sky:#cee9f5;
  --mint:#cfeae6;
  --navy:#3277b5;
  --ink:#111;
  --text:#555;
  --rule:#d9dde0;
  --star:#f7941d;
  --footer-bg:#f1f1f1;
  --footer-bar:#eaeaea;
}
*{box-sizing:border-box;margin:0;padding:0}
html,body{width:756px;height:1200px;overflow:hidden}
body{position:relative;font-family:"Montserrat",sans-serif;color:var(--text);background:#fff}
.page-bg{position:absolute;left:0;top:0;width:756px;height:420px;background:linear-gradient(#dbf1fb 0,#eef8fd 280px,#fff 420px)}
.header-curve{position:absolute;left:0;top:0}
.top-line{position:absolute;left:0;top:0;width:756px;height:1.5px;background:var(--navy)}

.brand{position:absolute;left:102px;top:12px;display:flex;align-items:center;gap:10px}
.brand-mark{width:51px;height:28px;background:var(--blue-soft);border-radius:3px}
.brand-name{font-weight:700;color:var(--blue);font-size:12.5px;line-height:14px;letter-spacing:.3px}

.main-nav{position:absolute;left:251px;top:25px;display:flex;gap:11.6px;font-size:6.6px;font-weight:500;color:#444;letter-spacing:.1px}
.main-nav .active{color:var(--green)}

.call-badge{position:absolute;left:545px;top:-11px;width:71px;height:72px;border-radius:50%;background:var(--navy);color:#fff;text-align:center}
.call-badge svg{position:absolute;left:27px;top:20px}
.call-badge span{position:absolute;left:0;right:0;top:40px;font-size:8px;font-weight:600}

.lang-switch{position:absolute;left:623px;top:18px;width:32px;height:19px;border-radius:2px;background:var(--green);color:#fff;font-size:6.5px;display:flex;align-items:center;justify-content:center;gap:3px}

.page-title{position:absolute;left:0;width:756px;top:137px;text-align:center;font-size:27px;font-weight:800;color:var(--ink);letter-spacing:.5px}
.page-intro{position:absolute;left:210px;width:336px;top:176px;text-align:center;font-size:6.8px;line-height:12.5px}

.review{position:absolute;left:102px;width:554px;border-bottom:.6px solid var(--rule)}
.review p{font-size:6.7px;font-weight:400;line-height:12.3px;padding-left:1px}
.review .by{display:flex;align-items:center;gap:4px;margin-top:12px;font-size:7px;font-weight:600;padding-left:1px}
.review:last-of-type{border-bottom:none}
.by.navy{color:var(--navy)} .by.blue{color:var(--blue)} .by.green{color:var(--green)}

.footer-bg{position:absolute;left:0;top:972px;width:756px;height:228px;background:var(--footer-bg)}
.cta{position:absolute;left:102px;top:918px}
.cta-tag{position:absolute;left:115px;top:954px;font-size:6.8px;color:#fff}
.cta-title{position:absolute;left:115px;top:964px;font-size:22.5px;font-weight:700;color:#fff;letter-spacing:.6px}
.cta-button{position:absolute;left:494px;top:968px;width:141px;height:28px;border-radius:14px;background:#fff;color:#222;font-size:7.6px;font-weight:700;display:flex;align-items:center;justify-content:center;letter-spacing:.3px}

.footer-brand{position:absolute;left:102px;top:1052px;width:122px;text-align:center}
.footer-brand .mark{width:50px;height:50px;margin:0 auto 9px;background:var(--blue-soft);border-radius:4px}
.footer-brand .name{font-size:10.6px;font-weight:700;color:var(--blue);white-space:nowrap}
.social{position:absolute;left:113px;top:1123px;display:flex;gap:5px}
.social span{width:21px;height:21px;border-radius:50%}

.footer-col{position:absolute;top:1051px;font-size:6.6px;line-height:11.8px}
.footer-col h3{font-size:7.5px;font-weight:700;color:#333;letter-spacing:.3px;margin-bottom:6px}
.links{left:246px}
.hours{left:389px}
.hours table{border-collapse:collapse}
.hours td{padding:0;line-height:11.8px}
.hours td+td{padding-left:5px;font-weight:700;color:#333}
.contact{left:533px;width:124px}
.contact .row{position:relative;padding-left:15px}
.contact .row svg{position:absolute;left:0;top:2px}
.contact .phone{font-size:9.5px;margin:4px 0 10px}

.footer-bar{position:absolute;left:0;top:1171px;width:756px;height:29px;background:var(--footer-bar);font-size:6.8px;color:#999}
.footer-bar .copy{position:absolute;left:102px;top:11px}
.footer-bar .copy b{font-weight:400;color:var(--navy)}
.footer-bar .partner{position:absolute;right:102px;top:11px;color:var(--green)}
</style>
</head>
<body>
<svg width="0" height="0" style="position:absolute">
  <defs>
    <symbol id="star" viewBox="0 0 24 24"><path d="M12 1.5l3.1 6.9 7.4.7-5.6 5 1.7 7.4L12 17.7 5.4 21.5l1.7-7.4-5.6-5 7.4-.7z" fill="#f7941d"/></symbol>
    <symbol id="stars" viewBox="0 0 60 12"><use href="#star" x="0" width="11" height="11"/><use href="#star" x="12" width="11" height="11"/><use href="#star" x="24" width="11" height="11"/><use href="#star" x="36" width="11" height="11"/><use href="#star" x="48" width="11" height="11"/></symbol>
    <linearGradient id="ctaGrad" x1="0" x2="1" y1="0" y2="0"><stop offset="0" stop-color="#0592cd"/><stop offset="1" stop-color="#00a990"/></linearGradient>
  </defs>
</svg>

<div class="page-bg"></div>
<svg class="header-curve" width="756" height="100" viewBox="0 0 756 100"><path d="M0 0H756V43Q560 95 378 95Q196 95 0 43Z" fill="#fff"/></svg>
<div class="top-line"></div>

<header>
  <div class="brand"><span class="brand-mark"></span><span class="brand-name">THE BRIGHT ARCH<br>CLINIC</span></div>
  <nav class="main-nav"><span>HOME</span><span>MEET US</span><span>SERVICES</span><span>PATIENT INFO</span><span class="active">REVIEWS</span><span>BLOG</span><span>CONTACT</span></nav>
  <div class="call-badge">
    <svg width="15" height="15" viewBox="0 0 24 24"><path d="M6.6 10.8a15.1 15.1 0 006.6 6.6l2.2-2.2a1 1 0 011-.25 11.4 11.4 0 003.6.6 1 1 0 011 1V20a1 1 0 01-1 1A17 17 0 013 4a1 1 0 011-1h3.5a1 1 0 011 1c0 1.25.2 2.45.6 3.6a1 1 0 01-.25 1z" fill="#fff"/></svg>
    <span>617.555.0142</span>
  </div>
  <div class="lang-switch">汉语 <svg width="6" height="4" viewBox="0 0 6 4"><path d="M.5.5L3 3 5.5.5" stroke="#fff" fill="none" stroke-width="1"/></svg></div>
</header>

<main>
  <h1 class="page-title">REVIEWS</h1>
  <p class="page-intro">Lorem Ipsum is dummy text of the printing and typesetting industry. Lorem Ipsum has been the industry's standard dummy text.</p>

  <article class="review" style="top:236px;height:111px">
    <p>I have been patient of Dr. Marlow for quite some time and I wholeheartedly recommend him! He is dedicated to his patient's wellfare and will do anything in his power to prevent more complicated procedures like root canals. I've had a lot of issues that he managed to solve while preserving the integrity of my teeth and for that, I am really grateful. The entire staff of The Bright Arch Clinic are truly great people-attentive, caring and compassionate. I've never had any issues with appointments or waiting, and prices have been more than fair. Special shout out to Dr. Petrov-awesome surgeon who managed to somehow extract a super twisted widom tooth. Many thanks!</p>
    <div class="by navy">– Theo R <svg width="59" height="12"><use href="#stars"/></svg></div>
  </article>
  <article class="review" style="top:373px;height:59px">
    <p>Friendly staff, pleasant atmosphere, great on time, and a very engaged doctor. Highly recommended!</p>
    <div class="by blue">– Priya Anand <svg width="59" height="12"><use href="#stars"/></svg></div>
  </article>
  <article class="review" style="top:458px;height:59px">
    <p>Amazing place. I wish they had dental services for adults;)</p>
    <div class="by green">– Marta Velasco <svg width="59" height="12"><use href="#stars"/></svg></div>
  </article>
  <article class="review" style="top:543px;height:59px">
    <p>Both of my boys have been treated here. Great service. I recommend them to a friend.</p>
    <div class="by blue">– Owen Halvorsen <svg width="59" height="12"><use href="#stars"/></svg></div>
  </article>
  <article class="review" style="top:628px;height:64px">
    <p>Great service. Everyone was so friendly!</p>
    <div class="by navy">– Jonah Brenner <svg width="59" height="12"><use href="#stars"/></svg></div>
  </article>
  <article class="review" style="top:718px;height:74px">
    <p>I have been coming to see Dr. Lindqvist for over a year now. She has been nothing but amazing! Her staff is wonderful and makes you feel like you're family from the moment you walk in the door. I cannot say enough good things about her and her office!</p>
    <div class="by blue">– Claire Dunmore <svg width="59" height="12"><use href="#stars"/></svg></div>
  </article>
  <article class="review" style="top:817px;height:60px">
    <p>I LOVE everyone at this office!! Dr. Lindqvist is the best of the best. The office staff are always courteous and kind, even kept an eye on my granddaughter who was watching TV while I was being seen. They are professional, nice, outgoing, friendly--just what every office strives to be--they have it all!!</p>
    <div class="by green">– Ruth Ellison <svg width="59" height="12"><use href="#stars"/></svg></div>
  </article>
</main>

<footer>
  <div class="footer-bg"></div>
  <svg class="cta" width="554" height="106" viewBox="0 0 554 106"><path d="M5 0L548 28Q554 28.3 554 34V101Q554 106 549 106H5Q0 106 0 101V5Q0 0 5 0Z" fill="url(#ctaGrad)"/></svg>
  <p class="cta-tag">Lorem Ipsum is dummy text of the printing and typesetting.</p>
  <p class="cta-title">YOUR SMILE. OUR PASSION.</p>
  <div class="cta-button">BOOK AN APPOINTMENT</div>

  <div class="footer-brand"><div class="mark"></div><div class="name">THE BRIGHT ARCH CLINIC</div></div>
  <div class="social">
    <span style="background:var(--blue)"></span><span style="background:var(--navy)"></span><span style="background:var(--green)"></span><span style="background:#3bbad3"></span>
  </div>

  <div class="footer-col links">
    <h3>USEFUL LINKS</h3>
    <div>Home</div><div>Meet Us</div><div>Services</div><div>Patient Info</div><div>Case &amp; Reviews</div><div>Blog</div><div>Contact</div>
  </div>

  <div class="footer-col hours">
    <h3>OPENING HOURS</h3>
    <table>
      <tr><td>Sunday &amp; Monday</td><td>Closed</td></tr>
      <tr><td>Tuesday</td><td>9:30AM – 5:00PM</td></tr>
      <tr><td>Wednesday</td><td>Closed</td></tr>
      <tr><td>Thursday</td><td>9:30AM – 5:00PM</td></tr>
      <tr><td>Friday</td><td>9:00AM – 5:00PM</td></tr>
      <tr><td>Saturday</td><td>9:00AM – 5:00PM</td></tr>
    </table>
  </div>

  <div class="footer-col contact">
    <h3>CONTACT INFO</h3>
    <div class="row"><svg width="7" height="10" viewBox="0 0 14 20"><path d="M7 0a7 7 0 017 7c0 5-7 13-7 13S0 12 0 7a7 7 0 017-7z" fill="#00a990"/><circle cx="7" cy="7" r="2.6" fill="#f1f1f1"/></svg>270 Harbor Lane, Suite 12, Fairview MA 02110</div>
    <div class="row phone"><svg width="9" height="9" viewBox="0 0 24 24"><path d="M6.6 10.8a15.1 15.1 0 006.6 6.6l2.2-2.2a1 1 0 011-.25 11.4 11.4 0 003.6.6 1 1 0 011 1V20a1 1 0 01-1 1A17 17 0 013 4a1 1 0 011-1h3.5a1 1 0 011 1c0 1.25.2 2.45.6 3.6a1 1 0 01-.25 1z" fill="#3277b5"/></svg>617.555.0142</div>
    <div class="row"><svg width="10" height="7" viewBox="0 0 20 14"><rect width="20" height="14" rx="1.5" fill="#33a6d7"/><path d="M1 1.5l9 6.5 9-6.5" stroke="#fff" stroke-width="1.5" fill="none"/></svg>info@thebrightarchclinic.com</div>
  </div>

  <div class="footer-bar">
    <span class="copy">© <b>The Bright Arch Clinic</b> - 2019. All Rights  Reserved.</span>
    <span class="partner">Harborview Skin Studio</span>
  </div>
</footer>
</body>
</html>
```